business card deign

Logo needs the following on it.
1. attached logo
2. Tagline - "If it keeps a drink cold or the party going...we do it!"
3. Name- Dalton Pikes, Founder and CPO
4. Address - 412 E. Carver Avenue, Ste 2207, Tampa, FL. 33917
5. Phone - 555.318.4726

```html
<!DOCTYPE html>
<html lang="en">
<head>
<meta charset="utf-8">
<title>Business Card – Front and Back</title>
<link href="https://fonts.googleapis.com/css2?family=Roboto:wght@400;700;900&display=swap" rel="stylesheet">
<style>
  :root{
    --stage:#232323;
    --card:#111111;
    --card-edge:#1c1c1c;
    --ink:#ffffff;
    --ink-soft:#e6e6e6;
    --shade:#2a2a2a;
  }
  *{box-sizing:border-box;margin:0;padding:0}
  html,body{width:1200px;height:711px;overflow:hidden;background:var(--stage)}
  body{font-family:"Roboto",Arial,sans-serif;color:var(--ink);position:relative}
  .card{
    position:absolute;top:205px;width:525px;height:300px;border-radius:22px;
    background:var(--card);border:1px solid var(--card-edge);
    box-shadow:0 18px 40px rgba(0,0,0,.55);overflow:hidden;
  }
  .card--front{left:50px}
  .card--back{left:625px}

  .brand{display:flex;align-items:center;gap:12px}
  .brand__dot{width:16px;height:16px;border-radius:50%;background:var(--ink)}
  .brand__name{font-weight:900;letter-spacing:.32em;color:var(--ink)}

  .card--front .brand{position:absolute;left:0;right:0;top:0;bottom:0;justify-content:center}
  .card--front .brand__name{font-size:40px}

  .card--back .brand{position:absolute;left:36px;top:58px}
  .card--back .brand__dot{width:12px;height:12px}
  .card--back .brand__name{font-size:26px}

  .identity{position:absolute;right:38px;top:28px;text-align:right}
  .identity__name{font-size:22px;font-weight:700}
  .identity__role{font-size:12.5px;color:var(--ink-soft);margin-top:3px}
  .identity__bar{position:absolute;right:0;top:24px;width:16px;height:52px;background:var(--ink)}

  .tagline{position:absolute;left:36px;top:128px;font-size:12.5px;line-height:1.5;color:var(--ink-soft);width:240px}
  .contact{position:absolute;left:36px;top:190px;list-style:none;font-size:12.5px;line-height:1.55;color:var(--ink-soft)}
  .contact li{display:flex;align-items:flex-start;gap:9px}
  .contact svg{width:13px;height:13px;margin-top:3px;flex:none}
</style>
</head>
<body>
  <section class="card card--front" aria-label="Card front">
    <div class="brand">
      <span class="brand__dot"></span>
      <span class="brand__name">BRISKLY</span>
    </div>
  </section>

  <section class="card card--back" aria-label="Card back">
    <div class="identity">
      <p class="identity__name">Dalton Pikes</p>
      <p class="identity__role">Founder and CPO</p>
    </div>
    <span class="identity__bar"></span>

    <div class="brand">
      <span class="brand__dot"></span>
      <span class="brand__name">BRISKLY</span>
    </div>

    <p class="tagline">If it keeps a drink cold or<br>the party going...we do it!</p>

    <ul class="contact">
      <li>
        <svg viewBox="0 0 24 24" fill="none" stroke="currentColor" stroke-width="2"><path d="M5 3h4l2 5-3 2a12 12 0 0 0 6 6l2-3 5 2v4a2 2 0 0 1-2 2A18 18 0 0 1 3 5a2 2 0 0 1 2-2z"/></svg>
        <span>555.318.4726</span>
      </li>
      <li>
        <svg viewBox="0 0 24 24" fill="none" stroke="currentColor" stroke-width="2"><path d="M12 22s7-7 7-12a7 7 0 0 0-14 0c0 5 7 12 7 12z"/><circle cx="12" cy="10" r="2.5"/></svg>
        <span>412 E. Carver Avenue,<br>Ste 2207, Tampa, FL. 33917</span>
      </li>
    </ul>
  </section>
</body>
</html>
```